business card for a massage therapy practice named 'Cedar and Willow Massage Studio'

I really need a trendy, yet easy on the eyes business card to complement my logo. Ideally with some gold or rose gold foil work.

My uploaded file of the logo I have in horizontal but I have a vertical version as well. Another color that is used in the website is a blush pink here and there. I'd like to see some trendy tropical leaves in the design.

```html
<!DOCTYPE html>
<html lang="en">
<head>
<meta charset="utf-8">
<title>Cedar and Willow Massage Studio – Business Card</title>
<link href="https://fonts.googleapis.com/css2?family=Montserrat:wght@400;500;600;700&display=swap" rel="stylesheet">
<style>
  :root{
    --canvas:#e4e5e7;
    --paper:#ffffff;
    --mint:#7cc6ad;
    --gold:#927c52;
    --ink:#1f1f1f;
    --grey:#555555;
    --pattern-base:#f3f1ea;
    --pattern-leaf:#a8cfb6;
    --pattern-fruit:#c9b88f;
  }
  *{margin:0;padding:0;box-sizing:border-box}
  html,body{width:1200px;height:857px;overflow:hidden}
  body{
    background:var(--canvas);
    font-family:"Montserrat",Arial,sans-serif;
    display:flex;align-items:center;justify-content:center;gap:40px;
  }
  .card{
    position:relative;width:540px;height:309px;background:var(--paper);
    box-shadow:0 6px 18px rgba(0,0,0,.12);overflow:hidden;
  }
  .card__swoosh{position:absolute;inset:0;width:100%;height:100%}
  .brand{
    position:absolute;display:flex;align-items:center;gap:10px;
  }
  .brand__dot{width:26px;height:26px;border-radius:50%;background:var(--gold);flex:none}
  .brand__name{
    font-weight:600;color:var(--ink);font-size:17px;line-height:1.2;letter-spacing:.2px;
  }
  .front .brand{left:34px;top:38px;width:300px}
  .contact{position:absolute;left:40px;top:170px;color:var(--grey)}
  .contact__name{
    font-weight:700;color:var(--gold);font-size:16px;letter-spacing:1px;text-transform:uppercase;
  }
  .contact__role{font-size:11px;letter-spacing:1.5px;text-transform:uppercase;margin-bottom:14px;color:var(--grey)}
  .contact__line{font-size:12px;line-height:1.45}
  .contact__label{color:var(--gold);font-weight:500}
  .back__pattern{
    position:absolute;inset:0;
    background:
      radial-gradient(circle at 30% 40%,var(--pattern-leaf) 0,transparent 60%),
      radial-gradient(circle at 70% 70%,var(--pattern-fruit) 0,transparent 60%),
      var(--pattern-base);
  }
  .back__frame{
    position:absolute;left:110px;top:86px;width:320px;height:137px;
    background:var(--paper);border:1.5px solid var(--mint);
    display:flex;align-items:center;justify-content:center;
  }
  .back__frame .brand{position:static;width:250px}
</style>
</head>
<body>

  <section class="card front">
    <svg class="card__swoosh" viewBox="0 0 540 309" preserveAspectRatio="none" aria-hidden="true">
      <rect width="540" height="309" fill="var(--mint)"/>
      <path d="M0 0 H398 C505 50 520 210 330 309 H0 Z" fill="var(--gold)"/>
      <path d="M0 0 H388 C495 52 508 208 318 309 H0 Z" fill="var(--paper)"/>
      <path d="M0 0 H384 C490 54 502 206 312 309 H0 Z" fill="var(--paper)" stroke="var(--paper)"/>
    </svg>
    <div class="brand">
      <span class="brand__dot"></span>
      <span class="brand__name">Cedar and Willow Massage Studio</span>
    </div>
    <div class="contact">
      <p class="contact__name">Marisol Venter</p>
      <p class="contact__role">Manager</p>
      <p class="contact__line"><span class="contact__label">Phone:</span> 555-014-2290</p>
      <p class="contact__line"><span class="contact__label">Email:</span> hello@cwmassage.com</p>
      <p class="contact__line"><span class="contact__label">Web:</span> www.cwmassage.com</p>
    </div>
  </section>

  <section class="card back">
    <div class="back__pattern" role="img" aria-label="Repeating pattern of small gold and green tropical fruit motifs"></div>
    <div class="back__frame">
      <div class="brand">
        <span class="brand__dot"></span>
        <span class="brand__name">Cedar and Willow Massage Studio</span>
      </div>
    </div>
  </section>

</body>
</html>
```